Simple but elegant business card/logo design for exclusive beauty business

We need a logo designed for a new elegant and exclusive beauty business called "G". The logo itself should be a stylistic and custom design for the letter "G". We would like the business card to have the logo as the centrepiece on a clean background. Gold Logo on black background or silver on white background.

The business card details should be displayed centre of the card. Details are as follows:

Marla Vance
Facebook: /simplyshinebym
Instagram: /simplyshinebym

The words "Simply Shine" should also appear somewhere on the card.

Industry/Entity Type

Business

Logo Text

G

Requirements
Must have
• Design must be simple, clean and elegant
Should not have
• The design should not be cluttered

```html
<!DOCTYPE html>
<html lang="en">
<head>
<meta charset="utf-8">
<title>Simply Shine – Business Card</title>
<link rel="stylesheet" href="https://fonts.googleapis.com/css2?family=Montserrat:wght@400;600&family=Open+Sans:wght@400;600&display=swap">
<style>
  :root {
    --backdrop: #1c1c1c;
    --card: #0f0f0f;
    --card-edge: #262626;
    --gold: #c9973f;
    --gold-soft: #a8782c;
  }
  * { margin: 0; padding: 0; box-sizing: border-box; }
  html, body { width: 1200px; height: 660px; overflow: hidden; }
  body {
    background: var(--backdrop);
    position: relative;
    font-family: "Open Sans", sans-serif;
  }
  .card {
    position: absolute;
    top: 180px;
    width: 520px;
    height: 300px;
    background: var(--card);
    border: 1px solid var(--card-edge);
    box-shadow: 0 14px 30px rgba(0,0,0,.55);
  }
  .card--front { left: 50px; }
  .card--back { left: 630px; }

  .front-mark {
    position: absolute;
    inset: 0;
    display: flex;
    align-items: center;
    justify-content: center;
    font-family: "Montserrat", sans-serif;
    font-weight: 600;
    font-size: 34px;
    color: var(--gold);
    letter-spacing: 1px;
  }

  .wordmark {
    position: absolute;
    left: 40px;
    top: 122px;
    width: 210px;
    font-family: "Montserrat", sans-serif;
    font-weight: 600;
    font-size: 30px;
    line-height: 1.05;
    color: var(--gold);
  }
  .divider {
    position: absolute;
    left: 278px;
    top: 60px;
    width: 2px;
    height: 180px;
    background: linear-gradient(to bottom, transparent, var(--gold) 20%, var(--gold) 80%, transparent);
  }
  .details {
    position: absolute;
    left: 302px;
    top: 78px;
    color: var(--gold);
  }
  .details__name {
    font-family: "Montserrat", sans-serif;
    font-size: 17px;
    margin-bottom: 10px;
  }
  .details__name strong { font-weight: 600; }
  .details__name span { font-weight: 400; }
  .contact { list-style: none; }
  .contact__item {
    display: flex;
    align-items: center;
    gap: 8px;
    font-size: 11px;
    line-height: 1;
    margin-bottom: 7px;
  }
  .contact__item--gap { margin-top: 10px; }
  .contact__icon { width: 11px; height: 11px; flex: none; }
  .contact__square {
    width: 10px; height: 10px; flex: none;
    background: var(--gold-soft);
  }
</style>
</head>
<body>
  <section class="card card--front" aria-label="Card front">
    <div class="front-mark">Simply Shine</div>
  </section>

  <section class="card card--back" aria-label="Card back">
    <div class="wordmark">Simply Shine</div>
    <div class="divider"></div>
    <div class="details">
      <p class="details__name"><strong>Marla</strong> <span>Vance</span></p>
      <ul class="contact">
        <li class="contact__item">
          <svg class="contact__icon" viewBox="0 0 12 12"><rect x="3" y="0.5" width="6" height="11" rx="1" fill="none" stroke="#c9973f"/><circle cx="6" cy="9.5" r=".7" fill="#c9973f"/></svg>
          0400 555 019
        </li>
        <li class="contact__item">
          <svg class="contact__icon" viewBox="0 0 12 12"><rect x="0.5" y="2" width="11" height="8" fill="#c9973f"/><path d="M0.5 2 L6 7 L11.5 2" fill="none" stroke="#0f0f0f"/></svg>
          simplyshinebym@mailbox.com
        </li>
        <li class="contact__item contact__item--gap">
          <span class="contact__square"></span>
          /simplyshinebym
        </li>
        <li class="contact__item">
          <span class="contact__square"></span>
          /simplyshinebym
        </li>
      </ul>
    </div>
  </section>
</body>
</html>
```